Anzeigengestaltung für Fliesenlegermeister
Zielgruppe
Ich bin ein Fliesenlegermeister und möchte mich selbstständig machen, ich saniere Bäder, Böden mit Fliesen, Fliesenspiegel und ich möchte eine Anzeige in den regionalen Zeitungen machen. Ich spreche alle Altersklassen mit Bädern für Sanierungen, Bodenfliesen und Neubauten an. Reparatur und Silikonarbeiten sowie Trockenbauarbeiten am eigenen Heim .
Aufgabenstellung
Ich möchte gern meine Kontaktdaten und die Farben vom Logo wieder finden,
als Beispiel habe ich meine aktuelle Visitenkarte beigefügt Dort finden sich die Kontaktdaten. Meine Arbeiten sind insbesondere :
Fliesenverlegung
Badsanierung
barrierefreie Bäder
Reparaturarbeiten
Silikonarbeiten
Trockenbau
Ob nun genau alle 6 Punkte in der Anzeige angezeigt werden soll bin ich mir nicht sicher oder ob nur 4 Beschreibungen reichen, damit es nicht zu viel wird.

```html
<!DOCTYPE html>
<html lang="de">
<head>
<meta charset="utf-8">
<title>Jonas Verhoff – Fliesenlegermeister</title>
<link href="https://fonts.googleapis.com/css2?family=Lato:wght@400;700;900&family=Covered+By+Your+Grace&display=swap" rel="stylesheet">
<style>
  :root {
    --brand-blue: #1d57a3;
    --brand-grey: #4a4a4a;
    --text-grey: #474747;
    --tab-grey: #4d4d4d;
    --row-bg: #fbf6f7;
    --page-bg: #ffffff;
  }
  html, body {
    margin: 0;
    padding: 0;
    overflow: hidden;
    background: var(--page-bg);
  }
  .ad {
    position: relative;
    width: 737px;
    height: 1200px;
    overflow: hidden;
    background: var(--page-bg);
    font-family: "Lato", sans-serif;
  }
  .brand {
    position: absolute;
    left: 0;
    top: 0;
    width: 737px;
    height: 160px;
  }
  .brand-mark {
    position: absolute;
    left: 72px;
    top: 30px;
    width: 96px;
    height: 96px;
    background: var(--brand-blue);
  }
  .brand-divider {
    position: absolute;
    left: 206px;
    top: 40px;
    width: 4px;
    height: 96px;
    background: var(--brand-grey);
  }
  .brand-name {
    position: absolute;
    left: 228px;
    top: 36px;
    margin: 0;
    font-weight: 900;
    font-size: 54px;
    line-height: 1;
    letter-spacing: 1px;
    color: var(--brand-blue);
    text-transform: uppercase;
  }
  .brand-title {
    position: absolute;
    left: 230px;
    top: 104px;
    margin: 0;
    font-weight: 700;
    font-size: 24px;
    line-height: 1;
    letter-spacing: 3.2px;
    color: var(--brand-grey);
    text-transform: uppercase;
  }
  .headline {
    position: absolute;
    left: 0;
    top: 225px;
    width: 737px;
    margin: 0;
    text-align: center;
    font-family: "Covered By Your Grace", cursive;
    font-weight: 400;
    font-size: 96px;
    line-height: 1;
    color: var(--brand-blue);
  }
  .services {
    position: absolute;
    left: 0;
    top: 398px;
    margin: 0;
    padding: 0;
    list-style: none;
  }
  .service {
    position: relative;
    height: 90px;
    padding-left: 191px;
    font-size: 49px;
    line-height: 70px;
    color: var(--text-grey);
  }
  .service::before {
    content: "";
    position: absolute;
    left: 89px;
    top: 28px;
    width: 18px;
    height: 18px;
    border-radius: 50%;
    background: var(--text-grey);
  }
  .contact {
    position: absolute;
    left: 0;
    width: 737px;
    height: 44px;
    background: var(--row-bg);
  }
  .contact-phone { top: 990px; }
  .contact-mail { top: 1057px; }
  .contact-address { top: 1122px; }
  .contact-tab {
    position: absolute;
    left: 0;
    top: 0;
    width: 127px;
    height: 44px;
    background: var(--tab-grey);
  }
  .contact-tab svg {
    position: absolute;
    right: 16px;
    top: 9px;
    width: 26px;
    height: 26px;
  }
  .contact-text {
    position: absolute;
    left: 154px;
    top: 0;
    margin: 0;
    font-size: 29px;
    line-height: 44px;
    font-weight: 700;
    color: #2e2e2e;
    white-space: nowrap;
  }
  .contact-text .label { font-weight: 400; }
  .contact-address .contact-text { left: 147px; }
</style>
</head>
<body>
<div class="ad">
  <header class="brand">
    <div class="brand-mark"></div>
    <div class="brand-divider"></div>
    <h1 class="brand-name">Jonas Verhoff</h1>
    <p class="brand-title">Fliesenlegermeister</p>
  </header>

  <h2 class="headline">Ihr Profi für</h2>

  <ul class="services">
    <li class="service">Fliesenverlegung</li>
    <li class="service">Badsanierung</li>
    <li class="service">barrierefreie Bäder</li>
    <li class="service">Reperaturarbeiten</li>
    <li class="service">Silikonarbeiten</li>
    <li class="service">Trockenbau</li>
  </ul>

  <div class="contact contact-phone">
    <div class="contact-tab">
      <svg viewBox="0 0 24 24" aria-hidden="true"><path d="M6.6 2.5c.6-.2 1.2 0 1.5.6l1.7 3.4c.3.6.1 1.2-.4 1.6L8 9.2c.9 2.6 4.1 5.8 6.8 6.8l1.1-1.4c.4-.5 1-.7 1.6-.4l3.4 1.7c.6.3.8.9.6 1.5l-.7 2.5c-.2.6-.8 1-1.4 1C9.6 20.6 3.4 14.4 3.1 6.6c0-.6.4-1.2 1-1.4z" fill="none" stroke="#fff" stroke-width="1.6" stroke-linejoin="round"/></svg>
    </div>
    <p class="contact-text">05301/4471920 <span class="label">Mobil</span> 01578294613</p>
  </div>

  <div class="contact contact-mail">
    <div class="contact-tab">
      <svg viewBox="0 0 24 24" aria-hidden="true"><rect x="3" y="6" width="18" height="12" rx="1" fill="none" stroke="#fff" stroke-width="1.6"/><path d="M3.5 6.5 12 13l8.5-6.5" fill="none" stroke="#fff" stroke-width="1.6"/></svg>
    </div>
    <p class="contact-text">info@fliesen-verhoff.de</p>
  </div>

  <div class="contact contact-address">
    <div class="contact-tab">
      <svg viewBox="0 0 24 24" aria-hidden="true"><path d="M12 2.5a6.5 6.5 0 0 0-6.5 6.5c0 4.8 6.5 12.5 6.5 12.5s6.5-7.7 6.5-12.5A6.5 6.5 0 0 0 12 2.5z" fill="none" stroke="#fff" stroke-width="1.8"/><circle cx="12" cy="9" r="2.4" fill="none" stroke="#fff" stroke-width="1.8"/></svg>
    </div>
    <p class="contact-text">Lindenweg 7, 38100 Musterstadt</p>
  </div>
</div>
</body>
</html>
```